Business card design needed

Family General Practitioner/ Family Physician.
Logo is the logo of the Noble Guild of Family Healers Oceania
http://kpltw.varendo.example/ImageShelf/marks/pages/NGFHO%20mark_jpg.htm
Updates

Project Deadline Extended
Reason: Just a bit more time to make changes and the weekend for me to look at things closely and to choose. Thanks, Orin

Thanks for all the submissions. So many of them are really works of art. Not one of them are not good. The ones that I am eliminating are the ones that I think are not suitable for me personally only, and because if I don't, it makes it very difficult to decide as many of you are also sending me slight variations of a card. I have just decided to choose a second place card too. Can't thank you all enough. Good luck, Orin. P.S - Working today till 10 pm as the card says :-), so probably won't be able to give a feedback till late Saturday night or Sunday morning here in Sydney, Australia. 

Project Deadline Extended
Reason: Just added a second place to the budget and realised that Australia is ahead of the rest of the world in the time zone (only :-) - don't want to offend anyone or start a debate!! ) , so Monday deadline will mean it will be a weekend for the rest of the world. Just wanted to give everyone more time to submit their best, especially since I will be picking a second card too. Can't thank everyone enough for the submissions. P.S - Not keen on photos on the card.

Industry/Entity Type

Business

Contact Information for Business Card

Dr. Orin Halvey M.B.B.S., F.N.G.F.H.O
Family General Practitioner
Address, timings, phone and fax number on the back.

Requirements
Must have
• Timings
Mon 7 am - 7 pm
Tues 7 am - 12 pm
Wed 7 am - 10 pm
Thurs 7 am - 12 pm
Fri 7 am - 8 pm
Sat 8 am - 10 pm
Sun - Off

```html
<!DOCTYPE html>
<html lang="en">
<head>
<meta charset="utf-8">
<title>Dr. Orin Halvey – Business Card</title>
<link href="https://fonts.googleapis.com/css2?family=Lato:ital,wght@0,400;0,700;1,400&family=Satisfy&display=swap" rel="stylesheet">
<style>
  :root {
    --backdrop: #e9e9eb;
    --card: #ffffff;
    --ink: #1a1a1a;
    --plum: #8e5a8c;
    --plum-text: #7d3f7f;
    --rule: #555555;
    --sketch-tone: #ececec;
  }
  * { box-sizing: border-box; margin: 0; padding: 0; }
  html, body {
    width: 1200px;
    height: 949px;
    overflow: hidden;
    background: var(--backdrop);
    font-family: "Lato", "Helvetica Neue", Arial, sans-serif;
    color: var(--ink);
  }
  .sheet {
    width: 1200px;
    height: 949px;
    display: flex;
    flex-direction: column;
    align-items: center;
    justify-content: center;
    gap: 50px;
  }
  .card {
    position: relative;
    width: 720px;
    height: 400px;
    background: var(--card);
    box-shadow: 0 4px 14px rgba(0,0,0,0.18);
    overflow: hidden;
  }
  .accent-square {
    position: absolute;
    left: 0;
    background: var(--plum);
  }
  .ground-rule {
    position: absolute;
    left: 0;
    width: 100%;
    height: 2px;
    background: var(--rule);
  }
  .family-sketch {
    position: absolute;
    background: linear-gradient(180deg, #f6f6f6, var(--sketch-tone));
    border-radius: 6px;
  }

  /* Back: timings */
  .card-back .accent-square { top: 72px; width: 82px; height: 56px; }
  .contact-lines {
    position: absolute;
    top: 38px;
    right: 42px;
    text-align: right;
    font-size: 21px;
    line-height: 1.25;
  }
  .timings {
    position: absolute;
    top: 78px;
    left: 100px;
  }
  .timings-title {
    color: var(--plum-text);
    font-weight: 700;
    font-size: 25px;
    line-height: 1.2;
    margin-bottom: 4px;
  }
  .schedule { border-collapse: collapse; font-size: 20px; line-height: 1.2; }
  .schedule th { text-align: left; font-weight: 400; padding: 1px 28px 1px 0; }
  .schedule td { padding: 1px 0; }
  .day-off {
    margin-top: 10px;
    margin-left: 30px;
    font-size: 27px;
    line-height: 1.2;
    font-weight: 700;
  }
  .card-back .family-sketch { left: 400px; top: 190px; width: 260px; height: 150px; }
  .card-back .ground-rule { top: 350px; }

  /* Front: identity */
  .tagline {
    position: absolute;
    top: 34px;
    right: 40px;
    font-family: "Satisfy", cursive;
    color: var(--plum-text);
    font-size: 30px;
  }
  .card-front .accent-square { top: 202px; width: 74px; height: 74px; }
  .identity { position: absolute; top: 204px; left: 82px; }
  .doctor-name { font-size: 25px; font-weight: 700; line-height: 1.2; }
  .credentials {
    font-style: italic;
    color: var(--plum-text);
    font-size: 17px;
    margin: 2px 0 0 8px;
    letter-spacing: 0.5px;
  }
  .role { font-size: 15px; margin-top: 4px; }
  .card-front .family-sketch { left: 370px; top: 200px; width: 250px; height: 150px; }
  .card-front .ground-rule { top: 350px; }
</style>
</head>
<body>
<main class="sheet">

  <section class="card card-back" aria-label="Card back: practice timings">
    <div class="accent-square"></div>
    <div class="contact-lines">
      <p>phone: 00 000000</p>
      <p>fax: 00 000000</p>
    </div>
    <div class="timings">
      <h2 class="timings-title">Timings:</h2>
      <table class="schedule">
        <tr><th>Mon</th><td>7 am - 7 pm</td></tr>
        <tr><th>Tues</th><td>7 am - 12 pm</td></tr>
        <tr><th>Wed</th><td>7 am - 10 pm</td></tr>
        <tr><th>Thurs</th><td>7 am - 12 pm</td></tr>
        <tr><th>Fri</th><td>7 am - 8 pm</td></tr>
        <tr><th>Sat</th><td>8 am - 10 pm</td></tr>
      </table>
      <p class="day-off">Sun - Off</p>
    </div>
    <div class="family-sketch" role="img" aria-label="Line sketch of a family: two parents with a baby in a pram and a small heart"></div>
    <div class="ground-rule"></div>
  </section>

  <section class="card card-front" aria-label="Card front: doctor details">
    <p class="tagline">"Caring about your health"</p>
    <div class="accent-square"></div>
    <div class="identity">
      <h1 class="doctor-name">Dr. Orin Halvey</h1>
      <p class="credentials">M.B.B.S., F.N.G.F.H.O</p>
      <p class="role">Family General Practitioner</p>
    </div>
    <div class="family-sketch" role="img" aria-label="Line sketch of a family: two parents with a baby in a pram and a small heart"></div>
    <div class="ground-rule"></div>
  </section>

</main>
</body>
</html>
```